Equine Podcast Cover Art Design

We need catchy cover art for a horse related podcast "Ride Onward Together"
Brief show description"
Whether you want to ride to experience horses, develop yourself to the next level as a horseman/horsewoman or ride to improve your physical and mental health, we are committed to helping you Ride Onward TogetherĀ®. Join us as we explore the nuance of equine management and sports as well as interview industry professionals to provide you with the knowledge necessary to be a better partner for your equine friends.
I have uploaded two existing logos we use for various purposes to give you an idea of existing style.
Target Market(s)
Horse owners and other equine professionals
Look and feel
Each slider illustrates characteristics of the customer's brand and the style your logo design should communicate.

```html
<!DOCTYPE html>
<html lang="en">
<head>
<meta charset="utf-8">
<title>Ride Onward Together – Podcast Cover</title>
<link href="https://fonts.googleapis.com/css2?family=Abril+Fatface&family=Bebas+Neue&display=swap" rel="stylesheet">
<style>
  :root {
    --navy: #24233f;
    --navy-deep: #1d1c36;
    --red: #b32334;
    --white: #ffffff;
    --sky: #b9c6d6;
    --gold: #c99a3c;
    --amber: #8a5a22;
    --shadow-brown: #2a1a10;
  }
  html, body {
    margin: 0;
    padding: 0;
    width: 1200px;
    height: 1200px;
    overflow: hidden;
    background: var(--navy);
  }
  .cover {
    position: relative;
    width: 1200px;
    height: 1200px;
    overflow: hidden;
    background: linear-gradient(180deg, var(--navy) 0%, var(--navy-deep) 100%);
  }
  .cover__photo {
    position: absolute;
    left: 724px;
    top: 0;
    width: 476px;
    height: 1200px;
    background: linear-gradient(180deg, var(--sky) 0%, #9fa98a 22%, var(--gold) 48%, var(--amber) 75%, var(--shadow-brown) 100%);
  }
  .cover__kicker {
    position: absolute;
    left: 96px;
    margin: 0;
    font-family: "Abril Fatface", serif;
    font-weight: 400;
    color: var(--red);
    line-height: 1;
    letter-spacing: -2px;
  }
  .cover__kicker--first { top: 40px; font-size: 190px; }
  .cover__kicker--second { top: 232px; font-size: 150px; }
  .cover__headline {
    position: absolute;
    left: 92px;
    top: 468px;
    margin: 0;
    font-family: "Bebas Neue", sans-serif;
    font-weight: 400;
    font-size: 300px;
    line-height: 1;
    color: var(--white);
    letter-spacing: 2px;
    transform: scaleY(1.7);
    transform-origin: top left;
  }
  .brand {
    position: absolute;
    left: 98px;
    top: 1010px;
    display: flex;
    align-items: center;
    gap: 14px;
  }
  .brand__dot {
    width: 34px;
    height: 34px;
    border-radius: 50%;
    background: var(--red);
  }
  .brand__name {
    font-family: "Abril Fatface", serif;
    font-size: 22px;
    color: var(--red);
    letter-spacing: 1px;
    line-height: 1.1;
    text-transform: uppercase;
  }
</style>
</head>
<body>
  <main class="cover">
    <div class="cover__photo" role="img" aria-label="Photograph of a rider in a helmet and dark jacket jumping a bay horse over a rail fence, autumn trees in warm light behind"></div>
    <p class="cover__kicker cover__kicker--first">Ride</p>
    <p class="cover__kicker cover__kicker--second">Onward</p>
    <h1 class="cover__headline">TOGETHER</h1>
    <div class="brand">
      <span class="brand__dot"></span>
      <span class="brand__name">Steadfast Meadow Farm</span>
    </div>
  </main>
</body>
</html>
```